Brochure for a paper wholesaler who wants to educate his print industry clients

We will be making a stapled informative brochure, that contains basic information about our paper products - the types of paper there is, their characteristics and other useful information.
As we are part of a paper wholesaler group in Europe - ORVALT, we received a brochure in German that has this kind of information. The text in it is not as important. What is important is the layout of the document and how the text will appear in it (added in the uploaded files - 210915_Wiessenswertes_TBKU_H73.pdf).
We are allowed to tinker with this file and adjust it to our needs. So there are also .idml and .indd files available (also in the uploaded files).
We would like to keep the custom page size of 210 x290mm (8.3x11.4 in), or you can go up to 210x297mm (8.3x11.7 in).
What we want is a modern looking design that contains our companies red bordo and white/ grey colours to replace the existing green colours in this borchure. The pictures and appearance of the file can be changed according to your views and what you think would look good. We don't necessarily want to keep the same design, we just want the layout of the document be the same, as we will be placing our translated text into it. The ORVALT logo should be replaced with our own logo (KENDRO Logo.png).
As for how it could look, it could go together with our paper presentation, for which the design can be seen in the "KENDRO Base - v2.pptx".
Holiday season, so have a lot of tasks to take care of and not as much time to check MakerHive as often.

```html
<!DOCTYPE html>
<html lang="de">
<head>
<meta charset="utf-8">
<title>Papierwissen – Broschüre Seite 4–5</title>
<link rel="stylesheet" href="https://fonts.googleapis.com/css2?family=Poppins:wght@400;500;600;700&display=swap">
<style>
  :root {
    --bordo: #8b2e2f;
    --bordo-soft: #c9a2a2;
    --ink: #1f1f1f;
    --paper: #ffffff;
    --band: #f2f2f2;
    --cell: #d9d9d9;
    --cell-light: #ececec;
    --stage: #0f0f0f;
  }
  * { margin: 0; padding: 0; box-sizing: border-box; }
  html, body { width: 1200px; height: 1200px; overflow: hidden; background: var(--stage); }
  body { position: relative; font-family: "Poppins", sans-serif; color: var(--ink); }

  .page { position: absolute; background: var(--paper); overflow: hidden; width: 565px; }
  .page--left { left: 34px; top: 168px; height: 780px; }
  .page--right { left: 604px; top: 167px; height: 783px; }

  /* Paper grade table */
  .grade-table {
    position: absolute; left: 47px; top: 44px; width: 478px;
    border-collapse: collapse; table-layout: fixed;
    font-size: 9px; line-height: 12.4px; text-align: center;
  }
  .grade-table th {
    background: var(--bordo); color: #fff; font-weight: 400; font-size: 9.8px;
    line-height: 11.4px; height: 29px; border-right: 1px solid #fff;
  }
  .grade-table td {
    background: var(--cell); border: 1px solid #fff; padding: 0 1px; vertical-align: middle;
    white-space: nowrap;
  }
  .grade-table .grade-name { font-weight: 700; }

  .rule { position: absolute; height: 2px; background: var(--bordo); }

  .section-title {
    position: absolute; color: var(--bordo); font-weight: 700; font-size: 18.4px;
    letter-spacing: -0.1px; line-height: 1;
  }
  .section-sub { position: absolute; font-weight: 600; font-size: 9.8px; line-height: 1; white-space: nowrap; }
  .lead {
    position: absolute; left: 47px; top: 418px;
    font-size: 9.9px; line-height: 12.4px; white-space: nowrap; letter-spacing: -0.05px;
  }

  .format-band { position: absolute; left: 0; width: 565px; background: var(--band); }
  .format-band--a { top: 479px; height: 201px; }
  .format-band--c { top: 0; height: 215px; }

  .format-list { position: absolute; font-size: 10px; line-height: 17.8px; }
  .format-list h3 { font-size: 9.8px; font-weight: 600; line-height: 17px; }
  .format-list dl { display: grid; grid-template-columns: 34px auto; }
  .format-list dt, .format-list dd { white-space: nowrap; }
  .format-list dl.indent-star dt { margin-left: -4px; }
  .format-note { font-size: 10px; line-height: 17.8px; white-space: nowrap; }

  .photo-strip {
    position: absolute; left: 0; top: 680px; width: 565px; height: 100px;
    background: linear-gradient(100deg, #5b4f47 0%, #a99e95 30%, #e6e2de 55%, #cfd3d9 80%, #eef0f3 100%);
  }

  .paper-stack-art {
    position: absolute; left: 441px; top: 142px; width: 78px; height: 56px;
    background: linear-gradient(160deg, var(--bordo-soft), var(--bordo));
    opacity: 0.55;
  }

  /* Thickness table */
  .thickness-table {
    position: absolute; left: 40px; top: 272px; width: 478px;
    border-collapse: collapse; table-layout: fixed; text-align: center;
    font-size: 9.6px;
  }
  .thickness-table th {
    background: var(--bordo); color: #fff; font-weight: 400; font-size: 9.6px;
    line-height: 11.4px; height: 32px; border-right: 1px solid #fff;
  }
  .thickness-table th:first-child { width: 101px; }
  .thickness-table td { height: 20.4px; border-right: 1px solid #fff; }
  .thickness-table tbody tr:nth-child(odd) td { background: var(--cell); }
  .thickness-table tbody tr:nth-child(even) td { background: var(--cell-light); }
  .thickness-table td:first-child { font-weight: 600; }

  .formula { position: absolute; left: 40px; top: 608px; font-size: 9.8px; }
  .formula .lhs { position: absolute; left: 0; top: 7px; white-space: nowrap; }
  .formula .num {
    position: absolute; left: 48px; top: 0; white-space: nowrap;
    border-bottom: 1px solid var(--ink); padding-bottom: 1px;
  }
  .formula .den { position: absolute; left: 213px; top: 19px; }

  .brand { position: absolute; left: 40px; top: 734px; display: flex; align-items: center; gap: 14px; }
  .brand-square { width: 24px; height: 32px; border: 1.5px solid var(--bordo); }
  .brand-name { color: var(--bordo); font-weight: 500; font-size: 12px; letter-spacing: 11px; }
  .tagline {
    position: absolute; left: 360px; top: 745px; font-size: 6.6px; font-weight: 600;
    letter-spacing: 1.2px; white-space: nowrap;
  }
  .page-number { position: absolute; left: 533px; top: 744px; font-size: 7px; font-weight: 700; color: var(--bordo); }
</style>
</head>
<body>

<section class="page page--left">
  <table class="grade-table">
    <colgroup>
      <col style="width:81px"><col style="width:73px"><col style="width:97px">
      <col style="width:75px"><col style="width:76px"><col style="width:76px">
    </colgroup>
    <thead>
      <tr><th colspan="2"></th><th>Strich</th><th>Bekannte<br>Bezeichnung</th><th>Kurz-<br>bezeichnung</th><th>Englische<br>Bezeichnung</th></tr>
    </thead>
    <tbody>
      <tr style="height:41px">
        <td class="grade-name" rowspan="2">Chromo-<br>Sulfatkarton</td>
        <td>Gebleicht –<br>weiß, gestri-<br>chen</td>
        <td>Einseitig oder zwei-<br>seitig zweifach<br>gestrichen</td>
        <td>Sulfatkarton=<br>Zellstoffkarton</td>
        <td>GZ, gestriche-<br>ner Zellstoff-<br>karton</td>
        <td>SBS board,<br>Solid Bleached<br>Sulfat Board</td>
      </tr>
      <tr style="height:79px">
        <td>Ungebleicht –<br>braun,<br>gestrichen</td>
        <td>Einseitig oder<br>zweiseitig gestri-<br>chen</td>
        <td>Kraftkarton</td>
        <td>GN 4,<br>gestrichener,<br>ungebleichter<br>Zellstoffkarton<br>mit brauner<br>Rückseite</td>
        <td>CNK, Coated<br>Natural Kraft<br>SUB, Solid<br>Unbleached<br>Board</td>
      </tr>
      <tr style="height:53px">
        <td class="grade-name" rowspan="2">Chromokarton</td>
        <td>Mit gestriche-<br>ner<br>weißer<br>Rückseite</td>
        <td>Einfach gestri-<br>chene Rückseite,<br>Vorderseite zwei-<br>fach gestrichen</td>
        <td>Faltschachtel-<br>karton</td>
        <td>GC 1,<br>gestrichener<br>Chromokarton</td>
        <td>FBB, Folding Box<br>Board coated<br>1 side</td>
      </tr>
      <tr style="height:54px">
        <td>Mit ungestri-<br>chener heller<br>Rückseite</td>
        <td>Helle, ungestri-<br>chene Rückseite,<br>Vorderseite zwei-<br>fach gestrichen</td>
        <td>Faltschachtel-<br>karton</td>
        <td>GC 2,<br>gestrichener<br>Chromokar-<br>ton 2</td>
        <td>FBB, Folding<br>Box Board with<br>manilla back</td>
      </tr>
      <tr style="height:42px">
        <td class="grade-name">Chromo-<br>Duplexkarton</td>
        <td>Mit grauer<br>Rückseite</td>
        <td>Rückseite pigmen-<br>tiert, Vorderseite<br>zweifach gestrichen</td>
        <td>Duplexkarton</td>
        <td>GD 2,<br>gestrichener<br>Duplexkarton 2</td>
        <td>WLC,<br>White Lined<br>Chipboard</td>
      </tr>
    </tbody>
  </table>

  <div class="rule" style="left:0; top:358px; width:525px;"></div>
  <h2 class="section-title" style="left:46px; top:372px;">DAS KLEINE 1X1 DER FORMATSCHULE</h2>
  <p class="section-sub" style="left:47px; top:401px;">Bogen-, DIN- und ORVALT Lagerformate</p>
  <p class="lead">Papierformate sind nach DIN genormt. Das Urformat der Reihe A ist ein Rechteck von 1 qm Größe.<br>Jedes weitere Format ergibt sich durch Halbieren oder Verdoppeln und hat ein Seitenverhältnis von<br>1:√2. Aus der DIN-Reihe A sind die DIN-Reihen B, C, und D abgeleitet. Die Rohformate, zur DIN-A-Rei-<br>he passend, werden ebenfalls als geläufige Formate gehandelt.</p>

  <div class="format-band format-band--a"></div>
  <div class="format-list" style="left:47px; top:484px;">
    <h3>DIN-A-Formate</h3>
    <dl>
      <dt>A0</dt><dd>841 x 1.189 mm</dd>
      <dt>A1</dt><dd>594 x 841 mm</dd>
      <dt>A2</dt><dd>420 x 595 mm</dd>
      <dt>A3</dt><dd>297 x 420 mm</dd>
      <dt>A4</dt><dd>210 x 297 mm</dd>
      <dt>A5</dt><dd>128 x 210 mm</dd>
      <dt>A6</dt><dd>105 x 148 mm</dd>
      <dt>A7</dt><dd>74 x 105 mm</dd>
    </dl>
  </div>
  <div class="format-list" style="left:251px; top:484px;">
    <h3>DIN-B-Formate</h3>
    <dl class="indent-star">
      <dt>B0</dt><dd>1.000 x 1.414 mm</dd>
      <dt>B1</dt><dd>707 x 1.000 mm</dd>
      <dt>B2</dt><dd>500 x 707 mm</dd>
      <dt>B3</dt><dd>353 x 500 mm</dd>
      <dt>*B4</dt><dd>250 x 353 mm</dd>
      <dt>*B5</dt><dd>176 x 250 mm</dd>
      <dt>*B6</dt><dd>125 x 176 mm</dd>
      <dt>B7</dt><dd>88 x 125 mm</dd>
    </dl>
    <p class="format-note" style="margin-top:3px; margin-left:-4px;">*Briefhüllen-/Versandtaschenformat</p>
  </div>

  <div class="photo-strip" role="img" aria-label="Foto: Hände blättern in einer aufgeschlagenen Zeitschrift"></div>
</section>

<section class="page page--right">
  <div class="format-band format-band--c"></div>
  <div class="format-list" style="left:45px; top:43px;">
    <h3>DIN-C-Formate</h3>
    <dl class="indent-star">
      <dt>C0</dt><dd>917 x 1.297 mm</dd>
      <dt>C1</dt><dd>648 x 917 mm</dd>
      <dt>C2</dt><dd>458 x 648 mm</dd>
      <dt>C3</dt><dd>324 x 458 mm</dd>
      <dt>*C4</dt><dd>229 x 324 mm</dd>
      <dt>*C5</dt><dd>162 x 229 mm</dd>
      <dt>*C6</dt><dd>114 x 162 mm</dd>
      <dt>C7</dt><dd>81 x 114 mm</dd>
    </dl>
  </div>
  <div class="format-list" style="left:254px; top:43px;">
    <h3>DIN-lang</h3>
    <dl class="indent-star">
      <dt>*DL</dt><dd>220 x 110 mm</dd>
    </dl>
    <p class="format-note" style="margin-left:-4px; line-height:12px;">*Briefhüllen-/Versandtaschenformat</p>
    <h3 style="margin-top:7px;">Rohformate, unbeschnitten</h3>
    <dl>
      <dt>A0</dt><dd>860 x 1.120 mm</dd>
      <dt>A1</dt><dd>610 x 860 mm</dd>
      <dt>A2</dt><dd>430 x 610 mm</dd>
      <dt>A3</dt><dd>305 x 430 mm</dd>
      <dt>A4</dt><dd>215 x 305 mm</dd>
    </dl>
  </div>
  <div class="paper-stack-art" role="img" aria-label="Illustration: Stapel Papierbögen mit umgeschlagener Ecke"></div>

  <div class="rule" style="left:40px; top:215px; width:525px;"></div>
  <h2 class="section-title" style="left:40px; top:229px;">UMFANGREICHE SACHE</h2>
  <p class="section-sub" style="left:40px; top:249px;">Die Buchdicke in Millimetern bei 100 Blatt in Abhängigkeit von Flächengewicht und Volumen</p>

  <table class="thickness-table">
    <thead>
      <tr>
        <th>Papiergewicht g/<br>qm</th><th>1,0-fach<br>100 Blatt</th><th>1,3-fach<br>100 Blatt</th><th>1,5-fach<br>100 Blatt</th>
        <th>1,8-fach<br>100 Blatt</th><th>2,0-fach<br>100 Blatt</th><th>2,2-fach<br>100 Blatt</th><th>2,5-fach<br>100 Blatt</th>
      </tr>
    </thead>
    <tbody>
      <tr><td>60</td><td>6,0</td><td>7,8</td><td>9,0</td><td>10,8</td><td>12,0</td><td>13,2</td><td>15,0</td></tr>
      <tr><td>70</td><td>7,0</td><td>9,1</td><td>10,5</td><td>12,6</td><td>14,0</td><td>15,4</td><td>17,5</td></tr>
      <tr><td>80</td><td>8,0</td><td>10,4</td><td>12,0</td><td>14,4</td><td>16,0</td><td>17,6</td><td>20,0</td></tr>
      <tr><td>90</td><td>9,0</td><td>11,7</td><td>13,5</td><td>16,2</td><td>18,0</td><td>19,8</td><td>22,5</td></tr>
      <tr><td>100</td><td>10,0</td><td>13,0</td><td>15,0</td><td>18,0</td><td>20,0</td><td>22,0</td><td>25,0</td></tr>
      <tr><td>110</td><td>11,0</td><td>14,3</td><td>16,5</td><td>19,8</td><td>22,0</td><td>24,2</td><td>27,5</td></tr>
      <tr><td>120</td><td>12,0</td><td>15,6</td><td>18,0</td><td>21,6</td><td>24,0</td><td>26,4</td><td>30,0</td></tr>
      <tr><td>135</td><td>13,5</td><td>17,6</td><td>20,3</td><td>24,3</td><td>27,0</td><td>29,7</td><td>33,8</td></tr>
      <tr><td>150</td><td>15,0</td><td>19,5</td><td>22,5</td><td>27,0</td><td>30,0</td><td>33,0</td><td>37,5</td></tr>
      <tr><td>170</td><td>17,0</td><td>22,1</td><td>25,5</td><td>30,6</td><td>34,0</td><td>37,4</td><td>42,5</td></tr>
      <tr><td>200</td><td>20,0</td><td>26,0</td><td>30,0</td><td>36,0</td><td>40,0</td><td>44,0</td><td>50,0</td></tr>
      <tr><td>250</td><td>25,0</td><td>32,5</td><td>37,5</td><td>45,0</td><td>50,0</td><td>55,0</td><td>62,5</td></tr>
      <tr><td>300</td><td>30,0</td><td>39,0</td><td>45,0</td><td>54,0</td><td>60,0</td><td>66,0</td><td>75,0</td></tr>
    </tbody>
  </table>

  <p class="section-sub" style="left:40px; top:593px;">Berechnung der Dicke des Buchblocks (D)</p>
  <div class="formula">
    <span class="lhs">D (mm)=</span>
    <span class="num">Blattzahl x Quadratmetergewicht (g/qm) x Volumen des Papiers (1,x-fach)</span>
    <span class="den">1.000</span>
  </div>

  <div class="brand">
    <span class="brand-square"></span>
    <span class="brand-name">KENDRO</span>
  </div>
  <p class="tagline">YOUR GROWTH IS OUR PRIORITY!</p>
  <p class="page-number">5</p>
</section>

</body>
</html>
```